Thriller/Romance novel book cover design - Copper Tidewake

I need a book cover for a novel (print + ebook). Genre = thriller / romance. Title = Copper Tidewake. Author = Dorian Kell.
Story is set in Caribbean. 45-year-old Ex-OVK agent is hunted by corrupt politicians, OVK and cartel. He is a life-long fisherman and seaman who joined the Army after college and became a war hero, followed by 10 years as operative for the OVK. Betrayal from Washington saw him accused of killing his mentor/friend/OVK Director and he is now a fugitive. He has been hiding for 7 years on Grand Cayman, and lives a secluded, private life as a fisherman on his modern sportfisherman-style boat ('50 Velmora Convertible for reference). Boat name = Copper Tidewake (as in the playing card) represents fate to him and his high school sweetheart to whom he was engaged before a tragic event separated them. His main goal, beyond survival, is to reunite with his long, lost love, but he can't risk putting her in danger until he settles the case and those searching for him. The boat name (Copper Tidewake) only has relevance to him and his soulmate, who is not even aware that he is still alive.

Target Market(s)

thriller and romantic thriller readers

Requirements
Must have
• author name should be small on bottom of cover - not at top. Design is wide open for creative ideas. If a boat is used in artwork, it must be a modern sportfisherman style boat (google will define this
Nice to have
• I like intrigue and mystery. Don't try to explain or show too much. Prefer sunsets (orange, red, purple, yellow) to blue sky, blue water to give it a darker tone
Should not have
• do not want images of people on the cover like many romance novels do.

```html
<!DOCTYPE html>
<html lang="en">
<head>
<meta charset="utf-8">
<title>Copper Tidewake — Dorian Kell</title>
<link href="https://fonts.googleapis.com/css2?family=EB+Garamond:wght@400;500&display=swap" rel="stylesheet">
<style>
  :root {
    --page: #ffffff;
    --ink-light: #ffffff;
    --sky-top: #3f2460;
    --sky-mid: #5a2f6e;
    --sky-magenta: #d8246a;
    --sky-red: #ef3b3a;
    --sky-orange: #f47a1f;
    --sky-gold: #f7c325;
    --sea-top: #6a2a78;
    --sea-mid: #3d2060;
    --sea-deep: #1f1638;
    --glow: #f6b52c;
    --plate: #3d7f96;
    --plate-ink: #10202a;
  }
  * { margin: 0; padding: 0; box-sizing: border-box; }
  html, body {
    width: 1200px; height: 1200px; overflow: hidden;
    background: var(--page);
  }
  .cover {
    position: absolute;
    left: 240px; top: 59px;
    width: 721px; height: 1081px;
    overflow: hidden;
    font-family: "EB Garamond", Georgia, serif;
  }
  .cover-art {
    position: absolute; inset: 0;
    background:
      radial-gradient(ellipse 90px 260px at 54% 80%, rgba(246,181,44,0.85), rgba(246,181,44,0) 70%),
      linear-gradient(to bottom,
        var(--sky-top) 0%,
        var(--sky-mid) 30%,
        var(--sky-magenta) 46%,
        var(--sky-red) 50%,
        var(--sky-orange) 54%,
        var(--sky-gold) 56%,
        var(--sky-orange) 58%,
        var(--sky-red) 59%,
        var(--sea-top) 59.3%,
        var(--sky-magenta) 66%,
        var(--sea-mid) 80%,
        var(--sea-deep) 100%);
  }
  .hull-shape {
    position: absolute; left: 0; top: 0;
  }
  .title {
    position: absolute; left: 0; right: 0; top: 40px;
    text-align: center;
    color: var(--ink-light);
    font-weight: 400;
    line-height: 0.9;
    text-shadow: 0 2px 3px rgba(0,0,0,0.35);
  }
  .title-line-small { display: block; font-size: 138px; letter-spacing: -1px; }
  .title-line-large { display: block; font-size: 168px; letter-spacing: -3px; margin-top: 8px; }
  .nameplate {
    position: absolute; left: 362px; top: 929px;
    width: 92px; height: 42px;
    background: var(--plate);
    border: 2px solid var(--plate-ink);
    transform: rotate(6deg);
    display: flex; align-items: center; justify-content: center;
    text-align: center;
    font-size: 12px; line-height: 1; font-weight: 500;
    color: var(--plate-ink);
  }
  .author {
    position: absolute; left: 0; right: 0; top: 978px;
    text-align: center;
    color: var(--ink-light);
    font-size: 54px;
    letter-spacing: 4px;
    font-weight: 400;
  }
</style>
</head>
<body>
  <main class="cover">
    <div class="cover-art" role="img" aria-label="Modern sportfisherman boat with tuna tower and outriggers, cabin lights glowing, floating on a calm sea under a purple, magenta, red and gold Caribbean sunset with a golden reflection on the water"></div>
    <h1 class="title">
      <span class="title-line-small">Copper</span>
      <span class="title-line-large">Tidewake</span>
    </h1>
    <div class="nameplate">Copper<br>Tidewake</div>
    <p class="author">Dorian Kell</p>
  </main>
</body>
</html>
```